Business Card Design for BrightvaleMedia.com

--I need a business card design for my company BrightvaleMedia.com

I have attached my logo...I want the brightvale media logo on the front of the business card, and then I want The Quillstone Chief on the back of it with my information.

I would like to see a light colored background as well as a dark colored background

FRONT:
BRIGHTVALE MEDIA LOGO
248 N. Larkmoor
3rd Floor
San Diego CA 92173
www.BrightvaleMedia.com

Advanced Website & App Development
Websites, Apps, Online Voucher Systems

Leading Edge Marketing Services
SMS, VB, SMM, SEM,

BACK:
QUILLSTONE CHIEF LOGO
Dorian Pelletta
The Quillstone Chief
Call Or Text: 619-555-0148
Dorian@QuillstoneChief.example
www.QuillstoneChief.example

Target Market(s)

small business owners

Industry/Entity Type

Business Consultant

Contact Information for Business Card

FRONT:
BRIGHTVALE MEDIA LOGO
248 N. Larkmoor
3rd Floor
San Diego CA 92173
www.BrightvaleMedia.com

SMS, VB, SMM, SEM,

BACK:
QUILLSTONE CHIEF LOGO
Dorian Pelletta
The Quillstone Chief
Dorian@QuillstoneChief.example
www.QuillstoneChief.example

Requirements
Must have
• add this quote on it somewhere, anywhere,preferrably on back
• "The Fastest Way To Success Is To Take Action”
• — Dorian Pelletta, Quillstone Chief
Nice to have
• open
Should not have
• red

```html
<!DOCTYPE html>
<html lang="en">
<head>
<meta charset="utf-8">
<title>Brightvale Media — Business Cards</title>
<link rel="stylesheet" href="https://fonts.googleapis.com/css2?family=Open+Sans:wght@400;600;700&display=swap">
<style>
  :root {
    --backdrop: #e9e7e3;
    --card-dark: #6b6c6e;
    --card-light: #ffffff;
    --brand-blue: #1d6fae;
    --ink-grey: #6b6c6e;
    --text-light: #f4f4f4;
    --rule-light: #c9cacc;
  }
  * { box-sizing: border-box; margin: 0; padding: 0; }
  html, body {
    width: 1200px; height: 900px; overflow: hidden;
    background: var(--backdrop);
    font-family: "Open Sans", Arial, sans-serif;
  }
  .card {
    position: absolute; left: 250px; width: 700px; height: 400px;
    box-shadow: 0 6px 18px rgba(0,0,0,.18);
    overflow: hidden;
  }
  /* Company side */
  .card--front { top: 35px; background: var(--card-dark); color: var(--text-light); text-align: center; }
  .company-name {
    margin-top: 62px;
    font-size: 44px; font-weight: 700; letter-spacing: 6px;
    color: var(--brand-blue);
  }
  .company-details { margin-top: 34px; font-size: 18px; line-height: 27px; }
  .company-rule { width: 560px; height: 1px; background: var(--rule-light); margin: 18px auto 12px; }
  .company-web { font-size: 18px; }

  /* Personal side */
  .card--back { top: 465px; background: var(--card-light); }
  .corner-mark { position: absolute; left: 0; top: 0; }
  .person { position: absolute; left: 92px; top: 30px; }
  .person-name { font-size: 21px; font-weight: 700; color: var(--brand-blue); }
  .person-title { font-size: 17px; color: var(--ink-grey); }
  .motto {
    position: absolute; right: 40px; top: 34px; width: 300px; text-align: right;
    font-size: 14px; line-height: 20px; color: var(--ink-grey);
  }
  .motto-source { display: block; margin-top: 4px; font-size: 13px; color: var(--brand-blue); }
  .personal-brand {
    position: absolute; right: 40px; top: 176px; white-space: nowrap;
    font-size: 32px; font-weight: 700; letter-spacing: 3px; color: var(--brand-blue);
  }
  .contact-list { position: absolute; left: 32px; top: 222px; list-style: none; }
  .contact-item {
    display: flex; align-items: center; gap: 12px;
    font-size: 18px; line-height: 27px; color: var(--ink-grey);
  }
  .contact-icon { width: 14px; height: 14px; flex: none; }
  .card-bands { position: absolute; left: 0; top: 0; }
</style>
</head>
<body>
  <section class="card card--front" aria-label="Company side">
    <h1 class="company-name">BRIGHTVALE MEDIA</h1>
    <div class="company-details">
      <p>248 N. Larkmoor</p>
      <p>3rd Floor, San Diego CA 92173</p>
      <p>Advanced Website &amp; App Development</p>
      <p>Websites | Apps | Online Voucher Systems</p>
      <p>Leading Edge Marketing Services | SMS | VB | SMM | SEM</p>
    </div>
    <div class="company-rule"></div>
    <p class="company-web">www.BrightvaleMedia.com</p>
  </section>

  <section class="card card--back" aria-label="Personal side">
    <svg class="corner-mark" width="80" height="60" viewBox="0 0 80 60" aria-hidden="true">
      <polygon points="0,0 42,0 0,48" fill="var(--brand-blue)"/>
      <polygon points="48,0 74,0 62,52 20,52" fill="var(--ink-grey)"/>
    </svg>
    <div class="person">
      <p class="person-name">Dorian Pelletta</p>
      <p class="person-title">The Quillstone Chief</p>
    </div>
    <blockquote class="motto">
      “The Fastest Way To Success Is To Take Action”
      <cite class="motto-source">— Dorian Pelletta, Quillstone Chief</cite>
    </blockquote>
    <p class="personal-brand">QUILLSTONE CHIEF</p>
    <ul class="contact-list">
      <li class="contact-item">
        <svg class="contact-icon" viewBox="0 0 14 14" aria-hidden="true"><path d="M3 1l2.5 3-1.5 1.5c.8 1.8 2 3 3.5 3.7L9 7.7l3 2.3-1.5 2.5C6 12 2 8 1.5 3.5z" fill="var(--brand-blue)"/></svg>
        619-555-0148
      </li>
      <li class="contact-item">
        <svg class="contact-icon" viewBox="0 0 14 14" aria-hidden="true"><rect x="1" y="3" width="12" height="8" fill="var(--brand-blue)"/><path d="M1 3l6 5 6-5" stroke="#fff" stroke-width="1" fill="none"/></svg>
        Dorian@QuillstoneChief.example
      </li>
      <li class="contact-item">
        <svg class="contact-icon" viewBox="0 0 14 14" aria-hidden="true"><circle cx="7" cy="7" r="6" fill="var(--brand-blue)"/><path d="M1 7h12M7 1c-3 3-3 9 0 12M7 1c3 3 3 9 0 12" stroke="#fff" stroke-width=".8" fill="none"/></svg>
        www.QuillstoneChief.example
      </li>
    </ul>
    <svg class="card-bands" width="700" height="400" viewBox="0 0 700 400" aria-hidden="true">
      <polygon points="0,328 318,328 302,346 0,346" fill="var(--brand-blue)"/>
      <polygon points="300,350 700,350 700,400 258,400" fill="var(--ink-grey)"/>
    </svg>
  </section>
</body>
</html>
```